verdant terraces simple classy business card design

my name is colin barrow and I run a gardening business aimed at high class verdant terraces. the business name is verdant terraces and our logo was designed on pixel harbour .My clientel are anything from residential homes to businesses. I take pride in my work and know that I offer a service like no other in my area.
The business card will be used to represent my business and I want it to be not only rememberable, but simplistic and modern. Eye catching too. Of course I would like it relatable to gardening and appealing to the correct clientel - those being garden enthusiasts, prestigious homes and businesses that are after top of the line gardening services like no other on the market.
I am not a typical lawn mowing business so I don't want a typical card design that represents that. The gardens I work with are generally million dollar properties with owners who are very garden proud looking for upkeep and guidance from me along with sometimes whole new garden designs. I want the business cards to show to my clients that I take pride, as they do, in their garden. And I want them to know from my card that I am a professional, qualified horticulturist offering them a top of the line service for life. I want them to refer my business on. I want them to look at my business card and see class and professionalism in a modern unique bold way.
The card should be simple with the possibility of the logo on the front being embossed/debossed and my details on the back the card should have a organic garden feel it's very important to me that it is absolutely perfect
I am also very open to ideas and suggestions so look forward to seeing the designs. the business logo has been supplied with this project and I want the card to be double sided

Contact info is
Colin Barrow - Managing Director / Horticulturist
Phone : 0481 526 704
Email: colinbarrow@verdantterraces.example.au

Target Market(s)

high class gardens residential and commercial

Industry/Entity Type

Gardener

Contact Information for Business Card

Contact info is
Phone : 0481 526 704

PLEASE MAKE CARD DOUBLE SIDED

Requirements
Must have
• organic simple classy modern feel
• must flow with the current logo that has been supplied with this project
• Double sided
• Must explain in a simple way that I deal with high end gardens and I'm a qualified horticulturist
Nice to have
• embossed debossed logo
Should not have
• shouldn't be to busy or cheap looking

```html
<!DOCTYPE html>
<html lang="en">
<head>
<meta charset="utf-8">
<title>Verdant Terraces – Business Card</title>
<link rel="stylesheet" href="https://fonts.googleapis.com/css2?family=Libre+Franklin:wght@400;500&display=swap">
<style>
  :root {
    --backdrop: #e6e7e8;
    --leaf-green: #55894a;
    --leaf-green-soft: #68985d;
    --card-white: #f1f2f3;
    --ink-white: #f4f6f3;
    --type: "Libre Franklin", Arial, sans-serif;
  }
  * { box-sizing: border-box; margin: 0; padding: 0; }
  html, body {
    width: 1105px;
    height: 1200px;
    overflow: hidden;
    background: var(--backdrop);
    font-family: var(--type);
  }
  .sheet {
    position: relative;
    width: 1105px;
    height: 1200px;
  }
  .card {
    position: absolute;
    left: 180px;
    width: 746px;
    height: 426px;
    overflow: hidden;
  }
  /* Details side */
  .card--details {
    top: 128px;
    background: var(--leaf-green);
    color: var(--ink-white);
  }
  .accent-bar {
    position: absolute;
    left: 0;
    top: 228px;
    width: 7px;
    height: 54px;
    background: var(--ink-white);
  }
  .person {
    position: absolute;
    left: 39px;
    top: 230px;
  }
  .person__name {
    font-size: 25px;
    font-weight: 500;
    letter-spacing: 0.2px;
    line-height: 30px;
  }
  .person__role {
    font-size: 20px;
    font-weight: 400;
    line-height: 30px;
  }
  .contact-list {
    position: absolute;
    left: 39px;
    top: 300px;
    list-style: none;
  }
  .contact-list__item {
    display: flex;
    align-items: center;
    gap: 10px;
    font-size: 18px;
    line-height: 28px;
  }
  .contact-list__icon {
    width: 17px;
    height: 17px;
    flex: none;
    fill: var(--ink-white);
  }
  .tree-artwork {
    position: absolute;
    left: 397px;
    top: 5px;
    width: 325px;
    height: 421px;
    background: linear-gradient(180deg, var(--leaf-green-soft) 0%, var(--leaf-green) 100%);
  }
  /* Brand side */
  .card--brand {
    top: 647px;
    background: var(--card-white);
    color: var(--leaf-green);
  }
  .brand {
    position: absolute;
    left: 0;
    right: 0;
    top: 113px;
    display: flex;
    flex-direction: column;
    align-items: center;
  }
  .brand__mark {
    width: 90px;
    height: 90px;
    border-radius: 50%;
    background: var(--leaf-green);
    margin-bottom: 18px;
  }
  .brand__name {
    font-weight: 500;
    text-align: center;
    line-height: 1;
  }
  .brand__name-line {
    display: block;
  }
  .brand__name-line--primary {
    font-size: 46px;
    letter-spacing: 9px;
    padding-left: 9px;
  }
  .brand__name-line--secondary {
    font-size: 24px;
    letter-spacing: 30px;
    margin-top: 10px;
    padding-left: 30px;
  }
</style>
</head>
<body>
<main class="sheet">
  <section class="card card--details" aria-label="Business card, details side">
    <div class="tree-artwork" role="img" aria-label="Area for white leafy tree illustration"></div>
    <span class="accent-bar"></span>
    <div class="person">
      <h1 class="person__name">Colin Barrow</h1>
      <p class="person__role">Managing Director / Horticulturist</p>
    </div>
    <ul class="contact-list">
      <li class="contact-list__item">
        <svg class="contact-list__icon" viewBox="0 0 24 24" aria-hidden="true">
          <path d="M4 7c0-2 3-4 8-4s8 2 8 4v2h-4V7.5c-1-.6-2.4-1-4-1s-3 .4-4 1V9H4z"/>
          <path d="M7 10h10l3 5v5H4v-5zm5 2.5a3 3 0 1 0 0 6 3 3 0 0 0 0-6z"/>
        </svg>
        <span>0481 526 704</span>
      </li>
      <li class="contact-list__item">
        <svg class="contact-list__icon" viewBox="0 0 24 24" aria-hidden="true">
          <path d="M2 5h20v2l-10 6L2 7z"/>
          <path d="M2 9l10 6 10-6v10H2z"/>
        </svg>
        <span>colinbarrow@verdantterraces.example.au</span>
      </li>
      <li class="contact-list__item">
        <svg class="contact-list__icon" viewBox="0 0 24 24" aria-hidden="true">
          <circle cx="12" cy="12" r="10"/>
          <path d="M8 6c2 0 3 2 2 3s-3 1-3 3 2 2 2 4-1 3-2 3M15 5c0 2 1 3 3 3M14 14c1-1 3-1 4 1s-1 3-2 4" stroke="var(--leaf-green)" stroke-width="1.6" fill="none"/>
        </svg>
        <span>verdantterraces.example.au</span>
      </li>
    </ul>
  </section>

  <section class="card card--brand" aria-label="Business card, brand side">
    <div class="brand">
      <span class="brand__mark" aria-hidden="true"></span>
      <p class="brand__name">
        <span class="brand__name-line brand__name-line--primary">VERDANT</span>
        <span class="brand__name-line brand__name-line--secondary">TERRACES</span>
      </p>
    </div>
  </section>
</main>
</body>
</html>
```